8x8 Social Media Ad - Brant Summit Expo

Attention Real Estate Agents
Please join us for our
Quarterly Real Estate Training Expo
The 2nd Saturday of February, May, August and November
Our Next Training Expo is _________________________________
From 9 am to 1 pm
at
Halvorne Suites Millbrook Court
4817 Copper Willow Lane, Dunmere, MD 20588
Scheduled Speakers
9:00 am - Marcus Pellington - Orientation
9:30 am - Derrin Oakfield - Multiple Income Streams / Crest Program
10:00 am - Talia Brennick - Marketing though Social Media
10:45 am - Rex Dunmore - Generating Business through Ru-Plaza
11:30 am - Kemi Adeyoro - Real Estate Investing
12:15 pm - Gregor Tamsey - (Main Speaker) Training Topic TBA
For more information call Marcus Pellington at (240) 555-0183 or email mpellington@brantsummithomes.example

```html
<!DOCTYPE html>
<html lang="en">
<head>
<meta charset="utf-8">
<title>Brant Summit Expo – Quarterly Real Estate Training Expo</title>
<link rel="stylesheet" href="https://fonts.googleapis.com/css2?family=Poppins:wght@300;400;500;600;700;800&family=Oswald:wght@500&display=swap">
<style>
  :root{
    --teal:#07899e;
    --teal-text:#0b8ea3;
    --cyan:#3fd0e8;
    --dark:#252525;
    --grey:#474747;
    --white:#ffffff;
    --photo-a:#c3c9e6;
    --photo-b:#8e97c2;
  }
  *{margin:0;padding:0;box-sizing:border-box}
  html,body{width:1200px;height:1080px;overflow:hidden;background:var(--white)}
  body{font-family:"Poppins",sans-serif;color:var(--grey)}
  .ad{position:relative;width:1200px;height:1080px;background:var(--white);overflow:hidden}
  .abs{position:absolute}

  .speaker-panel{left:692px;top:224px;width:508px;height:856px;background:var(--teal)}
  .footer-band{left:0;top:891px;width:692px;height:189px;background:var(--dark)}
  .banner{left:0;top:0;width:1200px;height:240px}

  .brand{left:73px;top:100px;display:flex;align-items:center;gap:12px}
  .brand-mark{width:34px;height:34px;background:var(--teal)}
  .brand-name{font-weight:600;font-size:21px;color:var(--dark);letter-spacing:.5px;text-transform:uppercase;line-height:1}

  .headline{left:0;top:0}
  .headline-main{position:absolute;left:903px;top:73px;font-weight:800;font-size:80px;line-height:1;color:var(--white);letter-spacing:1px;white-space:nowrap;transform:translateX(-50%);left:760px}
  .headline-sub{position:absolute;left:760px;top:160px;transform:translateX(-50%);font-weight:300;font-size:46px;line-height:1;color:var(--white);white-space:nowrap}

  .intro{left:73px;top:245px;font-weight:600;font-size:28px;color:var(--dark);white-space:nowrap}
  .title{left:70px;top:283px;font-weight:800;font-size:64px;line-height:57px;color:var(--grey);white-space:nowrap;letter-spacing:-.5px}
  .title .accent{color:var(--teal-text)}

  .date-label{left:74px;top:483px;width:376px;height:44px}
  .date-label span{position:absolute;left:27px;top:5px;font-weight:500;font-size:27px;color:var(--white);white-space:nowrap}

  .months{left:77px;top:536px;width:520px;height:80px}
  .month{position:absolute;display:flex;align-items:center;gap:8px;font-weight:700;font-size:35px;color:var(--grey);line-height:1}
  .month svg{flex:none}

  .next-label{left:73px;top:634px;font-weight:500;font-size:24px;color:var(--grey);white-space:nowrap}
  .date-field{left:74px;top:670px;width:506px;height:52px;border:2px solid #c9c9c9;border-radius:8px;background:var(--white)}
  .hours{left:73px;top:727px;font-weight:700;font-size:31px;color:var(--teal-text);white-space:nowrap}

  .venue{left:75px;top:790px;display:flex;gap:10px}
  .venue-text{font-weight:500;font-size:20px;line-height:23px;color:var(--grey)}

  .contact{left:75px;top:905px;color:var(--white)}
  .contact-lead{font-weight:300;font-size:20px;line-height:1.2}
  .contact-name{font-weight:700;font-size:31px;line-height:1.2;margin-bottom:10px}
  .contact-line{display:flex;align-items:center;gap:4px;font-weight:500;font-size:21px;line-height:27px}

  .speakers-title{left:777px;top:260px;font-family:"Oswald",sans-serif;font-weight:500;font-size:29px;letter-spacing:7.5px;color:var(--dark);white-space:nowrap}

  .speaker{position:absolute;left:642px;width:540px;height:104px}
  .speaker-photo{position:absolute;left:0;top:0;width:104px;height:104px;border-radius:50%;border:4px solid var(--white);background:radial-gradient(circle at 50% 40%,var(--photo-a),var(--photo-b));box-shadow:0 2px 6px rgba(0,0,0,.25)}
  .speaker-info{position:absolute;left:130px;top:16px;color:var(--white)}
  .speaker-name{font-weight:700;font-size:25px;line-height:1;text-transform:uppercase;white-space:nowrap}
  .speaker-topic{font-weight:400;font-size:16.5px;line-height:1;margin-top:7px;white-space:nowrap}
  .speaker-time{display:inline-block;margin-top:7px;padding:3px 5px;background:var(--dark);border-radius:3px;font-weight:500;font-size:16px;line-height:1.2}
  .divider{position:absolute;left:772px;width:360px;height:2px;background:rgba(0,0,0,.12)}
</style>
</head>
<body>
<main class="ad">

  <div class="abs speaker-panel"></div>
  <div class="abs footer-band"></div>

  <svg class="abs banner" width="1200" height="240" viewBox="0 0 1200 240" aria-hidden="true">
    <polygon points="491,52 1200,52 1200,224 422,224" fill="#252525"/>
    <polygon points="1030,34 1140,34 1153,50 1132,234 1046,234 1016,50" fill="#3fd0e8"/>
    <polygon points="1068,78 1103,78 1095,150 1076,150" fill="#ffffff"/>
    <ellipse cx="1086" cy="175" rx="19" ry="17" fill="#ffffff"/>
  </svg>

  <div class="abs brand">
    <div class="brand-mark"></div>
    <div class="brand-name">Brant Summit<br>Realty Group</div>
  </div>

  <div class="abs headline">
    <h1 class="headline-main">ATTENTION</h1>
    <p class="headline-sub">REAL ESTATE AGENTS</p>
  </div>

  <p class="abs intro">PLEASE JOIN US FOR OUR</p>
  <h2 class="abs title">QUARTERLY<br>REAL ESTATE<br><span class="accent">TRAINING EXPO</span></h2>

  <div class="abs date-label">
    <svg width="376" height="44" viewBox="0 0 376 44" aria-hidden="true"><polygon points="0,0 362,0 376,44 0,44" fill="#252525"/></svg>
    <span>The 2nd Saturday of</span>
  </div>

  <div class="abs months">
    <div class="month" style="left:0;top:0">
      <svg width="28" height="30" viewBox="0 0 28 30" aria-hidden="true"><rect x="6" y="0" width="4" height="6" fill="#0b8ea3"/><rect x="18" y="0" width="4" height="6" fill="#0b8ea3"/><rect x="0" y="4" width="28" height="8" rx="2" fill="#0b8ea3"/><rect x="0" y="14" width="28" height="16" rx="2" fill="#0b8ea3"/></svg>FEBRUARY</div>
    <div class="month" style="left:0;top:38px">
      <svg width="28" height="30" viewBox="0 0 28 30" aria-hidden="true"><rect x="6" y="0" width="4" height="6" fill="#0b8ea3"/><rect x="18" y="0" width="4" height="6" fill="#0b8ea3"/><rect x="0" y="4" width="28" height="8" rx="2" fill="#0b8ea3"/><rect x="0" y="14" width="28" height="16" rx="2" fill="#0b8ea3"/></svg>MAY</div>
    <div class="month" style="left:260px;top:2px">
      <svg width="28" height="30" viewBox="0 0 28 30" aria-hidden="true"><rect x="6" y="0" width="4" height="6" fill="#0b8ea3"/><rect x="18" y="0" width="4" height="6" fill="#0b8ea3"/><rect x="0" y="4" width="28" height="8" rx="2" fill="#0b8ea3"/><rect x="0" y="14" width="28" height="16" rx="2" fill="#0b8ea3"/></svg>AUGUST</div>
    <div class="month" style="left:260px;top:40px">
      <svg width="28" height="30" viewBox="0 0 28 30" aria-hidden="true"><rect x="6" y="0" width="4" height="6" fill="#0b8ea3"/><rect x="18" y="0" width="4" height="6" fill="#0b8ea3"/><rect x="0" y="4" width="28" height="8" rx="2" fill="#0b8ea3"/><rect x="0" y="14" width="28" height="16" rx="2" fill="#0b8ea3"/></svg>NOVEMBER</div>
  </div>

  <p class="abs next-label">OUR NEXT TRAINING EXPO IS</p>
  <div class="abs date-field"></div>
  <p class="abs hours">9 AM - 1 PM</p>

  <div class="abs venue">
    <svg width="50" height="60" viewBox="0 0 50 60" aria-hidden="true"><path d="M25 0C11.2 0 0 10.6 0 23.7 0 40 25 60 25 60S50 40 50 23.7C50 10.6 38.8 0 25 0Z" fill="#0b8ea3"/><circle cx="25" cy="22" r="10" fill="#ffffff"/></svg>
    <p class="venue-text">Halvorne Suites Millbrook Court<br>4817 Copper Willow Lane, Dunmere,<br>MD 20588</p>
  </div>

  <div class="abs contact">
    <p class="contact-lead">For more information call</p>
    <p class="contact-name">MARCUS PELLINGTON</p>
    <p class="contact-line">
      <svg width="20" height="20" viewBox="0 0 24 24" aria-hidden="true"><path d="M6.6 10.8a15.1 15.1 0 0 0 6.6 6.6l2.2-2.2c.3-.3.7-.4 1-.2 1.1.4 2.3.6 3.6.6.6 0 1 .4 1 1V20c0 .6-.4 1-1 1C10.6 21 3 13.4 3 4c0-.6.4-1 1-1h3.5c.6 0 1 .4 1 1 0 1.3.2 2.5.6 3.6.1.3 0 .7-.2 1Z" fill="#0b8ea3"/></svg>(240) 555-0183</p>
    <p class="contact-line">
      <svg width="20" height="16" viewBox="0 0 20 16" aria-hidden="true"><rect x="0" y="1" width="20" height="14" fill="#0b8ea3"/><polyline points="0,1 10,9 20,1" fill="none" stroke="#252525" stroke-width="1.5"/></svg>email mpellington@brantsummithomes.example</p>
  </div>

  <h3 class="abs speakers-title">SCHEDULED SPEAKERS</h3>

  <section class="speaker" style="top:300px">
    <div class="speaker-photo" role="img" aria-label="Portrait photo of speaker Marcus Pellington"></div>
    <div class="speaker-info"><p class="speaker-name">Marcus Pellington</p><p class="speaker-topic">Orientation</p><span class="speaker-time">9:00 am</span></div>
  </section>
  <div class="divider" style="top:414px"></div>

  <section class="speaker" style="top:422px">
    <div class="speaker-photo" role="img" aria-label="Portrait photo of speaker Derrin Oakfield"></div>
    <div class="speaker-info"><p class="speaker-name">Derrin Oakfield</p><p class="speaker-topic">Multiple Income Streams / Crest Program</p><span class="speaker-time">9:30 am</span></div>
  </section>
  <div class="divider" style="top:535px"></div>

  <section class="speaker" style="top:546px">
    <div class="speaker-photo" role="img" aria-label="Portrait photo of speaker Talia Brennick"></div>
    <div class="speaker-info"><p class="speaker-name">Talia Brennick</p><p class="speaker-topic">Marketing through Social Media</p><span class="speaker-time">10:00 am</span></div>
  </section>
  <div class="divider" style="top:656px"></div>

  <section class="speaker" style="top:667px">
    <div class="speaker-photo" role="img" aria-label="Portrait photo of speaker Rex Dunmore"></div>
    <div class="speaker-info"><p class="speaker-name">Rex Dunmore</p><p class="speaker-topic">Generating Business through Ru-Plaza</p><span class="speaker-time">10:45 am</span></div>
  </section>
  <div class="divider" style="top:777px"></div>

  <section class="speaker" style="top:788px">
    <div class="speaker-photo" role="img" aria-label="Portrait photo of speaker Kemi Adeyoro"></div>
    <div class="speaker-info"><p class="speaker-name">Kemi Adeyoro</p><p class="speaker-topic">Real Estate Investing</p><span class="speaker-time">11:30 am</span></div>
  </section>
  <div class="divider" style="top:899px"></div>

  <section class="speaker" style="top:910px">
    <div class="speaker-photo" role="img" aria-label="Portrait photo of main speaker Gregor Tamsey"></div>
    <div class="speaker-info"><p class="speaker-name">Gregor Tamsey</p><p class="speaker-topic">(Main Speaker) Training Topic TBA</p><span class="speaker-time">12:15 pm</span></div>
  </section>

</main>
</body>
</html>
```